Veldmark Supplies Business Card

Professional business card that stand out to our potential customers. Front and back with clean modern design

Industry/Entity Type

Oil and gas

Contact Information for Business Card

Name, address, website , office phone and cell number

Requirements
Must have
• Editable files for each employee

```html
<!DOCTYPE html>
<html lang="en">
<head>
<meta charset="utf-8">
<title>Veldmark Supplies Business Card</title>
<link rel="stylesheet" href="https://fonts.googleapis.com/css2?family=Roboto:wght@300;400;700;900&display=swap">
<style>
  :root {
    --backdrop: #7398c8;
    --navy: #1f2533;
    --red: #f40a0a;
    --red-soft: #e8253a;
    --cyan: #1aa9cf;
    --white: #ffffff;
    --ink: #4a4a4a;
    --ink-light: #9a9a9a;
    --pattern: #d9d9d9;
  }
  * { box-sizing: border-box; margin: 0; padding: 0; }
  html, body {
    width: 1200px; height: 912px; overflow: hidden;
    background: var(--backdrop);
    font-family: "Roboto", Arial, sans-serif;
  }
  .sheet {
    position: relative; width: 1200px; height: 912px;
    display: flex; align-items: center; justify-content: center; gap: 40px;
  }
  .card {
    position: relative; width: 520px; height: 297px; overflow: hidden;
    box-shadow: 0 10px 24px rgba(20, 40, 80, .25);
  }
  .card-band { position: absolute; inset: 0; width: 100%; height: 100%; }

  /* Back */
  .card-back { background: var(--navy); }
  .brand {
    position: absolute; display: flex; align-items: center; gap: 10px;
  }
  .brand-mark { width: 22px; height: 22px; background: var(--cyan); }
  .brand-name {
    font-weight: 900; text-transform: uppercase; letter-spacing: 1px;
  }
  .card-back .brand {
    left: 50%; top: 118px; transform: translateX(-50%);
  }
  .card-back .brand-name { color: var(--white); font-size: 26px; }

  /* Front */
  .card-front { background: var(--white); }
  .accent-bar {
    position: absolute; left: 0; top: 66px; width: 14px; height: 52px;
    background: var(--red-soft);
  }
  .holder { position: absolute; left: 44px; top: 58px; }
  .holder-name { font-size: 30px; font-weight: 900; color: var(--ink); letter-spacing: -.3px; }
  .holder-role { font-size: 12px; font-weight: 300; color: var(--ink-light); margin-top: 2px; }
  .line-pattern {
    position: absolute; left: 270px; top: 22px; width: 150px; height: 46px;
    background: var(--pattern); opacity: .6;
  }
  .card-front .brand { right: 26px; top: 40px; flex-direction: column; align-items: flex-end; gap: 6px; }
  .card-front .brand-mark { width: 34px; height: 34px; background: var(--cyan); }
  .card-front .brand-name { color: var(--red); font-size: 15px; }
  .contacts { position: absolute; left: 44px; top: 138px; list-style: none; }
  .contact {
    display: flex; align-items: center; gap: 12px;
    font-size: 13px; color: var(--ink); margin-bottom: 9px; line-height: 1.2;
  }
  .contact-icon {
    flex: none; width: 20px; height: 20px; border-radius: 3px;
    background: var(--cyan); display: flex; align-items: center; justify-content: center;
  }
  .contact-icon svg { width: 12px; height: 12px; }
</style>
</head>
<body>
<main class="sheet">

  <section class="card card-back" aria-label="Card back">
    <svg class="card-band" viewBox="0 0 520 297" aria-hidden="true">
      <polygon points="0,272 250,272 280,238 520,238 520,297 0,297" fill="var(--red)"/>
    </svg>
    <div class="brand">
      <span class="brand-mark"></span>
      <span class="brand-name">Veldmark Supplies</span>
    </div>
  </section>

  <section class="card card-front" aria-label="Card front">
    <div class="line-pattern" role="img" aria-label="Fine grey line pattern decoration"></div>
    <svg class="card-band" viewBox="0 0 520 297" aria-hidden="true">
      <polygon points="0,278 300,278 400,170 520,130 520,297 0,297" fill="var(--red)"/>
      <line x1="300" y1="297" x2="330" y2="250" stroke="var(--white)" stroke-width="5"/>
      <line x1="470" y1="160" x2="500" y2="140" stroke="var(--white)" stroke-width="5"/>
    </svg>
    <span class="accent-bar"></span>
    <div class="holder">
      <p class="holder-name">Marlow Bennett</p>
      <p class="holder-role">senior engineer</p>
    </div>
    <div class="brand">
      <span class="brand-mark"></span>
      <span class="brand-name">Veldmark Supplies</span>
    </div>
    <ul class="contacts">
      <li class="contact">
        <span class="contact-icon"><svg viewBox="0 0 12 12"><path d="M3 1 L5 3 L4 4.5 Q5 7 7.5 8 L9 7 L11 9 L9.5 11 Q3 10 1 2.5 Z" fill="#fff"/></svg></span>
        <span>(555)014-0273</span>
      </li>
      <li class="contact">
        <span class="contact-icon"><svg viewBox="0 0 12 12"><path d="M6 11 Q2 6.5 2 4.5 A4 4 0 0 1 10 4.5 Q10 6.5 6 11 Z" fill="#fff"/><circle cx="6" cy="4.5" r="1.5" fill="var(--cyan)"/></svg></span>
        <span>412 N.Harlan Ave Suite 5<br>Redmesa, Tx 79000</span>
      </li>
      <li class="contact">
        <span class="contact-icon"><svg viewBox="0 0 12 12" fill="none" stroke="#fff" stroke-width="1"><circle cx="6" cy="6" r="4.5"/><ellipse cx="6" cy="6" rx="2" ry="4.5"/><line x1="1.5" y1="6" x2="10.5" y2="6"/></svg></span>
        <span>www.veldmarksupplies.com</span>
      </li>
      <li class="contact">
        <span class="contact-icon"><svg viewBox="0 0 12 12"><rect x="1.5" y="3" width="9" height="6" fill="#fff"/><path d="M1.5 3 L6 6.5 L10.5 3" stroke="var(--cyan)" fill="none"/></svg></span>
        <span>sales@veldmarksupplies.com</span>
      </li>
    </ul>
  </section>

</main>
</body>
</html>
```